Cobalt Mend Works Business Cards

Create a business card for Cobalt Mend Works utilizing our new logo. We would like a QR Code for the easy of providing contact info to our customers. We would like our NTB CRS# as well as our ONRO # and our DTL #. I can provide all three numbers to you tomorrow.
I have attached two images of a similar business card.

```html
<!DOCTYPE html>
<html lang="en">
<head>
<meta charset="utf-8">
<title>Cobalt Mend Works – Business Card</title>
<link href="https://fonts.googleapis.com/css2?family=Arimo:wght@400;700&display=swap" rel="stylesheet">
<style>
  :root {
    --page-bg: #e4e4e4;
    --card-white: #ffffff;
    --card-dark-top: #3e3e3e;
    --card-dark-bottom: #303030;
    --navy: #173d7a;
    --sky: #1ba6e3;
    --ink: #4a4a4a;
    --white: #ffffff;
  }
  * { margin: 0; padding: 0; box-sizing: border-box; }
  html, body { width: 1200px; height: 1200px; overflow: hidden; }
  body {
    background: var(--page-bg);
    font-family: "Arimo", Arial, sans-serif;
    position: relative;
  }
  .card {
    position: absolute;
    left: 256px;
    width: 688px;
    height: 393px;
  }
  .card-front { top: 159px; background: var(--card-white); }
  .card-back {
    top: 653px;
    background: linear-gradient(180deg, var(--card-dark-top), var(--card-dark-bottom));
  }

  .identity {
    position: absolute;
    right: 394px;
    top: 147px;
    text-align: right;
    color: var(--ink);
    font-size: 17px;
    line-height: 21px;
    white-space: nowrap;
  }
  .identity .person-name {
    color: var(--navy);
    font-weight: 700;
    font-size: 28px;
    line-height: 32px;
    letter-spacing: 0.3px;
  }
  .identity .person-role {
    color: var(--sky);
    font-size: 16px;
    line-height: 20px;
    margin-bottom: 2px;
  }
  .divider {
    position: absolute;
    left: 311px;
    top: 156px;
    width: 2px;
    height: 82px;
    background: var(--navy);
  }
  .contact-list {
    position: absolute;
    left: 333px;
    top: 151px;
    list-style: none;
    color: var(--ink);
    font-size: 17px;
    line-height: 20.5px;
    white-space: nowrap;
  }
  .contact-list li { display: flex; align-items: center; gap: 8px; }
  .contact-list svg { width: 15px; height: 15px; fill: var(--navy); flex: none; }

  .brand-name {
    position: absolute;
    left: 0; right: 0;
    top: 160px;
    text-align: center;
    color: var(--white);
    font-weight: 700;
    font-size: 44px;
    letter-spacing: 3px;
    line-height: 54px;
  }
  .licences {
    position: absolute;
    left: 0; right: 0;
    top: 326px;
    text-align: center;
    color: var(--white);
    font-size: 17px;
    line-height: 20px;
    white-space: nowrap;
  }
  .licences .sep { margin: 0 6px; }
</style>
</head>
<body>
  <section class="card card-front">
    <div class="identity">
      <div class="person-name">ELLIS MARLOW</div>
      <div class="person-role">President</div>
      <div class="address">412 Larkspur Road</div>
      <div class="address">Fairbanks, Canada 21908</div>
    </div>
    <div class="divider"></div>
    <ul class="contact-list">
      <li>
        <svg viewBox="0 0 24 24" aria-hidden="true"><path d="M6.6 10.8a15.1 15.1 0 0 0 6.6 6.6l2.2-2.2a1 1 0 0 1 1-.25 11.4 11.4 0 0 0 3.6.57 1 1 0 0 1 1 1V20a1 1 0 0 1-1 1A17 17 0 0 1 3 4a1 1 0 0 1 1-1h3.5a1 1 0 0 1 1 1c0 1.25.2 2.45.57 3.57a1 1 0 0 1-.25 1z"/></svg>
        <span>604-281-7390</span>
      </li>
      <li>
        <svg viewBox="0 0 24 24" aria-hidden="true"><path d="M7 1h10a2 2 0 0 1 2 2v18a2 2 0 0 1-2 2H7a2 2 0 0 1-2-2V3a2 2 0 0 1 2-2zm0 3v14h10V4zm5 15.5a1 1 0 1 0 0 2 1 1 0 0 0 0-2z"/></svg>
        <span>604-395-1826</span>
      </li>
      <li>
        <svg viewBox="0 0 24 24" aria-hidden="true"><path d="M2 5h20v14H2zm2 2v.5l8 5 8-5V7zm0 2.8V17h16V9.8l-8 5z"/></svg>
        <span>info@cobaltmendworks.com</span>
      </li>
      <li>
        <svg viewBox="0 0 24 24" aria-hidden="true"><circle cx="12" cy="12" r="10"/><path d="M7 7c2 1 3 3 2 5s1 3 0 6M15 4c-1 2 1 3 3 3M14 13c2 0 3 2 2 5" stroke="#fff" stroke-width="1.6" fill="none"/></svg>
        <span>www.cobaltmendworks.com</span>
      </li>
    </ul>
  </section>

  <section class="card card-back">
    <div class="brand-name">COBALT MEND WORKS</div>
    <div class="licences">
      <span>NTB CRS#41873</span><span class="sep">|</span><span>ONRO#50291</span><span class="sep">|</span><span>DTL#67415</span>
    </div>
  </section>
</body>
</html>
```